Polystyrene Recycling Material Flow

We need a diagram styled as an infographic that shows how polystyrene foam is recycled starting with a manufactured product, moving through the distribution process, waste material collection and reincorporation back into manufacturing. This is accomplished in different ways once the material is collected which needs to be clearly evident. The most important thing is for it to be simple enough to understand while still having a stylish look. The design can be with or without vector images or photography to depict the different stages. We are providing a very rudimentary 'sketch' of the information points and movement flow. Please see www.foamtradecouncil.org (resources) to view our literature branding. The RGB & CMYK are attached.

Target Market(s)

Government Agencies, Brand Owners, Retailers, Recycling Industry

Industry/Entity Type

Packaging, Recycling, Manufacturing

Font styles to use
Sans Serif

Requirements
Must have
• Easy to Understand
Nice to have
• Images - either photography or vector illustrations - are optional. We have provided examples of both to show what could be used but are not required. Substituting your own interpretation of imagery is encouraged.
Should not have
• Outdated look.

```html
<!DOCTYPE html>
<html lang="en">
<head>
<meta charset="utf-8">
<title>Polystyrene Recycling Material Flow</title>
<link href="https://fonts.googleapis.com/css2?family=Roboto:wght@500;700&display=swap" rel="stylesheet">
<style>
  :root {
    --bg: #f2f2f2;
    --olive: #a3a813;
    --orange: #f5a01a;
    --steel: #5b87a5;
    --ink: #262626;
    --dots: #6f6f6f;
  }
  html, body { margin: 0; padding: 0; overflow: hidden; background: var(--bg); }
  .canvas { width: 1200px; height: 996px; display: block; }
  .flow-line { fill: none; stroke: var(--dots); stroke-width: 1.2; stroke-dasharray: 1.2 3; }
  .node { fill: var(--bg); stroke: var(--olive); stroke-width: 2.6; }
  .chevron { fill: none; stroke: var(--steel); stroke-width: 2.6; stroke-linecap: round; stroke-linejoin: round; }
  .step-box { fill: var(--olive); }
  .step-text { font-family: 'Roboto', sans-serif; font-weight: 700; font-size: 11.6px; fill: #ffffff; text-anchor: middle; dominant-baseline: central; }
  .stage-label { font-family: 'Roboto', sans-serif; font-weight: 500; font-size: 13.8px; fill: var(--ink); text-anchor: middle; }
  .hero-label { font-family: 'Roboto', sans-serif; font-weight: 500; font-size: 15px; fill: var(--ink); text-anchor: middle; }
  .item-label { font-family: 'Roboto', sans-serif; font-weight: 500; font-size: 11.8px; fill: var(--ink); }
  .diamond { stroke: var(--orange); stroke-width: 3.4; }
  .hero-ring { fill: none; stroke: var(--olive); stroke-width: 1.2; }
</style>
</head>
<body>
<svg class="canvas" viewBox="0 0 1200 996" xmlns="http://www.w3.org/2000/svg">
  <defs>
    <linearGradient id="sky-heap" x1="0" y1="0" x2="0" y2="1">
      <stop offset="0" stop-color="#b9c4cc"/><stop offset="0.45" stop-color="#d9c3a0"/><stop offset="1" stop-color="#5d5a55"/>
    </linearGradient>
    <linearGradient id="blue-belt" x1="0" y1="0" x2="0" y2="1">
      <stop offset="0" stop-color="#3d6f8f"/><stop offset="0.6" stop-color="#9cc6de"/><stop offset="1" stop-color="#2f9a63"/>
    </linearGradient>
    <linearGradient id="truck-load" x1="0" y1="0" x2="0" y2="1">
      <stop offset="0" stop-color="#b7cbe0"/><stop offset="0.5" stop-color="#e39a2a"/><stop offset="1" stop-color="#55595c"/>
    </linearGradient>
    <linearGradient id="dark-street" x1="0" y1="0" x2="1" y2="1">
      <stop offset="0" stop-color="#4f5d66"/><stop offset="1" stop-color="#23282c"/>
    </linearGradient>
    <linearGradient id="green-street" x1="0" y1="0" x2="1" y2="1">
      <stop offset="0" stop-color="#8fae6a"/><stop offset="1" stop-color="#2b3130"/>
    </linearGradient>
    <linearGradient id="worker-vest" x1="0" y1="0" x2="1" y2="1">
      <stop offset="0" stop-color="#6f8a54"/><stop offset="0.5" stop-color="#c9d24a"/><stop offset="1" stop-color="#4c5c6a"/>
    </linearGradient>
    <linearGradient id="yellow-bin" x1="0" y1="0" x2="0" y2="1">
      <stop offset="0" stop-color="#6b6a5c"/><stop offset="0.5" stop-color="#c9a22e"/><stop offset="1" stop-color="#2d2a26"/>
    </linearGradient>
    <linearGradient id="green-symbol" x1="0" y1="0" x2="1" y2="1">
      <stop offset="0" stop-color="#7a6a52"/><stop offset="0.5" stop-color="#5fbf4a"/><stop offset="1" stop-color="#4a3c30"/>
    </linearGradient>
    <linearGradient id="kitchen" x1="0" y1="0" x2="1" y2="1">
      <stop offset="0" stop-color="#e4e0da"/><stop offset="1" stop-color="#8e8a84"/>
    </linearGradient>
    <linearGradient id="bins-blue" x1="0" y1="0" x2="1" y2="0">
      <stop offset="0" stop-color="#3c8fd0"/><stop offset="1" stop-color="#e0a23a"/>
    </linearGradient>
    <linearGradient id="sea-heap" x1="0" y1="0" x2="0" y2="1">
      <stop offset="0" stop-color="#6e9c9a"/><stop offset="1" stop-color="#4a4338"/>
    </linearGradient>
    <linearGradient id="factory" x1="0" y1="0" x2="1" y2="1">
      <stop offset="0" stop-color="#3a4148"/><stop offset="0.6" stop-color="#d9a23a"/><stop offset="1" stop-color="#2c3034"/>
    </linearGradient>
    <linearGradient id="foam" x1="0" y1="0" x2="1" y2="1">
      <stop offset="0" stop-color="#dfe6ef"/><stop offset="1" stop-color="#bcc6cf"/>
    </linearGradient>
    <linearGradient id="office-bins" x1="0" y1="0" x2="0" y2="1">
      <stop offset="0" stop-color="#8a8b86"/><stop offset="1" stop-color="#6cb83a"/>
    </linearGradient>
    <linearGradient id="moss" x1="0" y1="0" x2="1" y2="1">
      <stop offset="0" stop-color="#5b7a3a"/><stop offset="1" stop-color="#2f4226"/>
    </linearGradient>
  </defs>

  <!-- connecting lines -->
  <g class="flow-lines">
    <path class="flow-line" d="M225 521 H293"/>
    <path class="flow-line" d="M259 198 V814 M259 198 H292 M259 816 H292"/>
    <path class="flow-line" d="M368 198 H440 M368 520 H440 M368 816 H440"/>
    <path class="flow-line" d="M440 106 V289 M440 106 H468 M440 197 H468 M440 289 H468"/>
    <path class="flow-line" d="M440 474 V566 M440 474 H468 M440 566 H468 M440 521 H637"/>
    <path class="flow-line" d="M440 816 H468"/>
    <path class="flow-line" d="M601 107 H637 M637 66 V149 M637 66 H656 M637 149 H656"/>
    <path class="flow-line" d="M601 286 H637 M637 245 V328 M637 245 H656 M637 328 H656"/>
    <path class="flow-line" d="M637 444 V597 M637 444 H656 M637 597 H656"/>
    <path class="flow-line" d="M718 444 H797 M856 444 H933 M718 592 H797"/>
    <path class="flow-line" d="M601 816 H637 M637 740 V892 M637 740 H656 M637 892 H656"/>
    <path class="flow-line" d="M718 740 H791 M718 892 H791 M791 740 V892 M791 817 H840"/>
  </g>

  <!-- chevrons -->
  <g class="chevrons">
    <path class="chevron" d="M402 192 L408 198 L402 204"/>
    <path class="chevron" d="M402 514 L408 520 L402 526"/>
    <path class="chevron" d="M402 810 L408 816 L402 822"/>
    <path class="chevron" d="M538 515 L544 521 L538 527"/>
    <path class="chevron" d="M751 438 L757 444 L751 450"/>
    <path class="chevron" d="M889 438 L895 444 L889 450"/>
    <path class="chevron" d="M751 586 L757 592 L751 598"/>
    <path class="chevron" d="M751 734 L757 740 L751 746"/>
    <path class="chevron" d="M751 886 L757 892 L751 898"/>
  </g>

  <!-- junction nodes -->
  <g class="nodes">
    <circle class="node" cx="259" cy="521" r="6"/>
    <circle class="node" cx="440" cy="198" r="6"/>
    <circle class="node" cx="440" cy="521" r="6"/>
    <circle class="node" cx="440" cy="816" r="6"/>
    <circle class="node" cx="637" cy="107" r="6"/>
    <circle class="node" cx="637" cy="286" r="6"/>
    <circle class="node" cx="637" cy="521" r="6"/>
    <circle class="node" cx="637" cy="816" r="6"/>
    <circle class="node" cx="791" cy="817" r="6"/>
  </g>

  <!-- hero -->
  <g class="hero">
    <circle class="hero-ring" cx="160" cy="521" r="62"/>
    <circle cx="160" cy="521" r="56" fill="url(#sky-heap)" role="img" aria-label="Photo of a large landfill heap of mixed waste under an evening sky"/>
    <text class="hero-label" x="160" y="606">EPS Collection</text>
  </g>

  <!-- stage diamonds -->
  <g class="stage">
    <rect class="diamond" x="303" y="171" width="54" height="54" rx="9" transform="rotate(45 330 198)" fill="url(#sky-heap)" role="img" aria-label="Photo of a landfill of mixed plastic waste"/>
    <text class="stage-label" x="330" y="254">EPS Waste</text>
    <text class="stage-label" x="330" y="270">Sources</text>
  </g>
  <g class="stage">
    <rect class="diamond" x="303" y="493" width="54" height="54" rx="9" transform="rotate(45 330 520)" fill="url(#blue-belt)" role="img" aria-label="Photo of plastic material on a sorting conveyor between compaction machines"/>
    <text class="stage-label" x="330" y="576">Compaction</text>
  </g>
  <g class="stage">
    <rect class="diamond" x="303" y="789" width="54" height="54" rx="9" transform="rotate(45 330 816)" fill="url(#truck-load)" role="img" aria-label="Photo of a yellow truck loaded with bags of recyclable waste"/>
    <text class="stage-label" x="330" y="872">Regrind-</text>
    <text class="stage-label" x="330" y="888">Molder Facilities</text>
  </g>

  <!-- process boxes -->
  <g class="steps">
    <rect class="step-box" x="470" y="89" width="126" height="35" rx="3"/>
    <text class="step-text" x="533" y="106.5">Municipal Waste</text>
    <rect class="step-box" x="470" y="179" width="126" height="35" rx="3"/>
    <text class="step-text" x="533" y="196.5">Manufacturing Waste</text>
    <rect class="step-box" x="470" y="269" width="126" height="35" rx="3"/>
    <text class="step-text" x="533" y="286.5">Commercial Waste</text>
    <rect class="step-box" x="470" y="456" width="126" height="35" rx="3"/>
    <text class="step-text" x="533" y="473.5">Extruded Ingot</text>
    <rect class="step-box" x="470" y="546" width="126" height="35" rx="3"/>
    <text class="step-text" x="533" y="563.5">Hydrolic Compression</text>
    <rect class="step-box" x="470" y="799" width="126" height="35" rx="3"/>
    <text class="step-text" x="533" y="816.5">Shredding</text>
  </g>

  <!-- collection channels -->
  <g class="channels">
    <circle cx="686" cy="67" r="30" fill="url(#dark-street)" role="img" aria-label="Photo of waste bins lined up along a street curb"/>
    <text class="item-label" x="725" y="72">Curbside Collection</text>
    <circle cx="686" cy="150" r="30" fill="url(#green-street)" role="img" aria-label="Photo of a collection truck at a drop-off point"/>
    <text class="item-label" x="725" y="155">Drop-Off Centers</text>
    <circle cx="686" cy="246" r="30" fill="url(#worker-vest)" role="img" aria-label="Photo of a worker in a safety vest loading bags of waste"/>
    <text class="item-label" x="725" y="251">Back Hauling</text>
    <circle cx="686" cy="328" r="30" fill="url(#yellow-bin)" role="img" aria-label="Photo of a yellow waste container on a delivery site"/>
    <text class="item-label" x="725" y="333">Localized Delivery</text>
  </g>

  <!-- compaction outputs -->
  <g class="outputs">
    <circle cx="686" cy="444" r="30" fill="url(#green-symbol)" role="img" aria-label="Photo of a green recycling arrows symbol surrounded by recycled items"/>
    <text class="item-label" x="663" y="487">Recycled Content</text>
    <text class="item-label" x="663" y="502">EPS Resin</text>
    <circle cx="825" cy="444" r="30" fill="url(#kitchen)" role="img" aria-label="Photo of a household sorting materials in a kitchen"/>
    <text class="item-label" x="802" y="487">Re-Pelletized With</text>
    <text class="item-label" x="802" y="502">Blowing Agent</text>
    <circle cx="961" cy="444" r="30" fill="url(#bins-blue)" role="img" aria-label="Photo of blue and yellow recycling bins"/>
    <text class="item-label" x="937" y="487">Expanded Polystyrene</text>
    <text class="item-label" x="937" y="502">Packaging &amp; Building Products</text>
    <circle cx="686" cy="592" r="30" fill="url(#sea-heap)" role="img" aria-label="Photo of a pile of mixed plastic waste"/>
    <text class="item-label" x="663" y="635">Extruded Rigid</text>
    <text class="item-label" x="663" y="650">PS Pellet</text>
    <circle cx="825" cy="592" r="30" fill="url(#factory)" role="img" aria-label="Photo of a factory worker in a hard hat sorting material"/>
    <text class="item-label" x="802" y="635">End Market</text>
    <text class="item-label" x="802" y="650">Applications</text>
  </g>

  <!-- regrind outputs -->
  <g class="regrind">
    <circle cx="686" cy="740" r="30" fill="url(#foam)" role="img" aria-label="Photo of shredded white foam pieces"/>
    <text class="item-label" x="663" y="783">Homogenization</text>
    <circle cx="686" cy="892" r="30" fill="url(#office-bins)" role="img" aria-label="Photo of green and yellow recycling bins in an office"/>
    <text class="item-label" x="663" y="931">Mixing for</text>
    <text class="item-label" x="663" y="946">Consistency</text>
    <circle cx="870" cy="817" r="30" fill="url(#moss)" role="img" aria-label="Photo of a recycling arrows symbol set in green moss"/>
    <text class="item-label" x="846" y="860">Recycled Content</text>
    <text class="item-label" x="846" y="875">Packaging</text>
  </g>
</svg>
</body>
</html>
```